Calder Aviation website

We are an aviation company based in Miramar, FL but with worldwide coverage. We are involved in commercial aircraft (mostly freighters) trading, sale & leasing. Specifically, we specialized in freighters of the Veltram family (V316, V328, V335, V342, V359). We also assist with financing, sale/leaseback. Handle special aviation projects and provide consultancy services. Currently engaged in a Veltram 359 passenger to Freighter conversion (P2F).

Website Preliminary Initial Content/Sections as follows:

About Us
Founded in 2011, Calder Aviation's management has many years of experience in Aviation, a strong background in scheduled airlines with emphasis in all cargo operations, freight forwarding supply chain and freight logistics, as well as ACMI and CMI operations.

Calder’s focuses in facilitating wet and dry lease operations, charter and ACMI programs consultancy, aircraft sales, leasing and procurement, aviation consultancy and aircraft management.

Calder team is a hands-on reliable alternative that works toward achieving your aircraft and aviation objectives by meeting your requirements and timeframe throughout professional and personalized service.

Tiberio Salcedo has over three decades of experience in the aviation field including aircraft maintenance, airline management, supply chain and logistics management. Tiberio is a true entrepreneur with proven experience and expertise on the multiple facets of the commercial aviation industry throughout the creation and development of a cluster of aviation entities. Tiberio is the founder and former sole member/chairman of 64 Air, a Veltram 342 All-Cargo U.S. Certificated Air Carrier created from scratch in 2014 which nowadays conforms a superb growing airline platform with an immaculate compliance operational record.

Services

Aircraft Finance, Trading, Procurement and Leasing
Calder buys, sells, leases and facilitates aircraft trading while specializes in structured aircraft investment projects. Calder has deep industry relationships and years of expertise, allowing to successfully execute lease transactions. We assist airlines, financial institutions and leasing companies when selling or purchasing aircraft.

Aircraft Available for Sale/Lease

Sale/Leaseback
Sale-leaseback is a method of financing. If your company needs liquidity, your aircraft or engine can serve as collateral for a loan throughout a sale-leaseback transaction. Sale-leaseback can free the equity tied up in aircraft or asset. Even if there is no pressing need for funds, a sale-leaseback allows you to use the equity tied up in your aircraft in a more productive fashion. Leaseback arrangements are usually employed because they confer financing, accounting or taxation benefits.

Passenger to Freighter Conversion (P2F)
Pandemic has seen the resurgence of operators packing freight into the main cabins of passenger aircraft. Carriers have been allowed to transport cargo in the cabin by removing passenger seats completely. NAB/CARO have established exemptions that allow operators to fly in “Preighter” configuration for a limited time. Calder is closely working with a U.S. group that is developing a Class E Supplemental Type Certificate (STC) for applicability on V359 aircraft which will include a cargo door for containerized freight. Final approvals are expected during first quarter of 2022.
Wet lease
Throughout our deep relationships within the industry, Calder facilitates short or long-term wet leases to airlines and qualified parties around the globe, whereby we provide the Aircraft, Crews, Maintenance and Insurance (ACMI) worldwide services at competitive rates. We also specialize in AM leases where the aircraft is registered onto Lessee´s AOC with all maintenance services included in the rates, covering all maintenance risks, or CM or CMI where the client provides the aircraft.

Dry Lease
We offer aircraft from our own portfolio on dry lease or could engage in procuring the aircraft of your choice.

Asset & Aircraft Management
We provide aircraft owners Aircraft Management services, where we manage the technical side of the aircraft or the asset. Calder also provides Harlow Dynamics engines trading, repair and full management services. We also buy Veltram/Skylane surplus inventory.

Worldwide Charters
We facilitate the arrangement of full charters to airlines and logistics companies. Certain territory restrictions may apply.

Aviation Consultancy
We provide airline consultancy services for new or special projects. Calder also specializes on All Cargo International route analysis, implementation and development. Our team provides professional guidance in obtaining worldwide both scheduled and charter authority.

Target Market(s)

Our target market are the airlines, logistics companies and commercial aviation related entities

Industry/Entity Type

Commercial Aviation

Coding

Coded - Design and coding required

Number of Pages Required

3 page

Requirements
Must have
• Illustrations of wide body freighters such V359, V342, V328

```html
<!DOCTYPE html>
<html lang="en">
<head>
<meta charset="utf-8">
<title>Calder Aviation</title>
<link href="https://fonts.googleapis.com/css2?family=Montserrat:wght@300;400;500;600&family=Playfair+Display:wght@400;700&family=Playfair+Display+SC:wght@400;700&display=swap" rel="stylesheet">
<style>
:root{
  --navy:#0b1740;
  --navy-deep:#07102e;
  --sky:#6aaed8;
  --white:#ffffff;
  --ink:#1b1b1b;
  --grey-btn:#3d4149;
  --ghost:#d2d2d2;
  --field:#d9d9d9;
  --muted:#555b66;
}
*{margin:0;padding:0;box-sizing:border-box}
html,body{width:1200px;height:3934px;overflow:hidden}
body{position:relative;font-family:'Montserrat',sans-serif;color:var(--ink);background:var(--white)}
.abs{position:absolute}
.serif{font-family:'Playfair Display',serif}
.sc{font-family:'Playfair Display SC',serif}

/* nav */
.topbar{left:0;top:0;width:1200px;height:98px;background:var(--navy)}
.brand{left:111px;top:22px;width:150px;color:var(--white);text-align:center;font-family:'Playfair Display',serif}
.brand .name{font-size:24px;letter-spacing:1px;line-height:28px}
.brand .sub{font-size:11px;letter-spacing:7px;border-top:1px solid var(--white);padding-top:3px}
.nav{left:372px;top:40px;display:flex;gap:36px;font-size:14px;color:var(--white)}
.btn-outline{border:1px solid var(--white);color:var(--white);font-size:14px;display:flex;align-items:center;justify-content:center}
.nav-cta{left:930px;top:30px;width:159px;height:38px;border-radius:2px}

/* hero */
.hero{left:0;top:98px;width:1200px;height:680px}
.hero-art{left:336px;top:176px;width:527px;height:236px;border-radius:40px;background:radial-gradient(ellipse at center,#e9eef6 0%,#b9c6dc 45%,rgba(106,174,216,0) 72%)}
.hero-kicker{left:0;top:482px;width:1200px;text-align:center;color:var(--white);font-weight:300;font-size:36px}
.hero-title{left:0;top:528px;width:1200px;text-align:center;color:var(--white);font-family:'Playfair Display',serif;font-weight:700;font-size:68px;letter-spacing:1px}
.btn-navy{background:var(--navy);color:var(--white);display:flex;align-items:center;justify-content:center;font-size:17px}
.hero-btn{left:511px;top:620px;width:178px;height:44px;border-radius:2px}
.dots{left:576px;top:686px;display:flex;gap:6px}
.dots i{width:7px;height:7px;border-radius:50%;background:var(--white);display:block}
.dots i.on{background:var(--navy)}

/* section heads */
.ghost{left:0;width:1200px;text-align:center;font-family:'Playfair Display',serif;color:var(--ghost);font-size:112px;line-height:1;letter-spacing:2px}
.sec-title{left:0;width:1200px;text-align:center;font-family:'Playfair Display',serif;font-size:56px;line-height:1}
.sec-sub{left:0;width:1200px;text-align:center;font-size:18px;line-height:30px;color:var(--muted)}

/* services */
.card{top:1009px;width:314px;height:512px;border:1px solid #d3d3d3;background:var(--white);text-align:center}
.card.lift{box-shadow:0 4px 14px rgba(0,0,0,.25)}
.card .ph{width:100%;height:255px}
.card h3{font-family:'Playfair Display',serif;font-weight:400;font-size:22px;margin-top:27px;letter-spacing:.5px}
.card p{font-size:13px;line-height:22px;margin:15px 24px 0}
.card .btn{margin:18px auto 0;width:143px;height:38px;background:var(--grey-btn);color:var(--white);font-size:15px;display:flex;align-items:center;justify-content:center}
.card.lift .btn{background:var(--navy)}

/* about */
.about{left:0;top:1637px;width:1200px;height:658px;background:linear-gradient(100deg,#101d4e 0%,#0b1740 50%,#0e1b4a 100%)}
.about-ghost{color:rgba(255,255,255,.08)}
.about-copy{left:111px;top:1900px;width:470px;color:var(--white);font-size:16px;line-height:25px}
.about-copy p+p{margin-top:25px}
.about-btn{left:111px;top:2158px;width:158px;height:36px;font-size:14px;border-radius:2px}
.about-media{left:620px;top:1900px;width:467px;height:310px;background:linear-gradient(180deg,#c9ced6 0%,#9aa2ad 55%,#4b5058 100%)}

/* blog */
.feature{left:111px;top:2561px;width:561px;height:377px;border-radius:12px;overflow:hidden;background:linear-gradient(180deg,#e3a6b4 0%,#8a6b8c 30%,#263049 55%,#05070d 80%,#000 100%)}
.feature h4{position:absolute;left:19px;bottom:63px;width:500px;color:var(--white);font-family:'Playfair Display SC',serif;font-weight:700;font-size:20px;line-height:31px}
.feature a{position:absolute;left:19px;bottom:24px;color:var(--white);font-size:15px;font-weight:600;text-decoration:underline}
.mini-ph{left:690px;width:162px;height:181px;border-radius:12px}
.mini-text{left:873px;width:220px}
.mini-text h4{font-family:'Playfair Display SC',serif;font-weight:400;font-size:21px;line-height:31px;letter-spacing:.5px}
.mini-text a{display:block;margin-top:20px;font-size:15px;font-weight:600;color:var(--ink);text-decoration:underline}

/* contact */
.contact{left:0;top:3088px;width:1200px;height:707px;background:linear-gradient(160deg,#5a3a1c 0%,#2f2214 35%,#14201c 65%,#0d2a26 85%,#10110e 100%)}
.contact-title{left:600px;top:3180px;width:487px;text-align:right;color:var(--white);font-family:'Playfair Display',serif;font-weight:700;font-size:44px;letter-spacing:2px}
.contact-info{left:600px;width:485px;text-align:right;color:var(--white);font-size:14px;line-height:27px}
.form{left:110px;top:3268px;width:477px;height:394px;background:var(--white);border-radius:2px}
.form h5{position:absolute;left:49px;top:28px;font-weight:400;font-size:22px}
.field{position:absolute;left:49px;width:379px;background:var(--field);font-size:12px;color:#666;padding:16px 27px}
.form .send{position:absolute;left:305px;top:328px;width:123px;height:35px;font-size:14px}
.socials{left:926px;top:3570px;display:flex;gap:10px}
.socials span{width:24px;height:24px;border-radius:50%;background:var(--white);display:block}
.contact-cta{left:960px;top:3628px;width:124px;height:35px;font-size:14px;border-radius:3px}

/* footer */
.footer{left:0;top:3795px;width:1200px;height:139px;background:#000}
.foot-nav{left:0;top:3833px;width:1200px;display:flex;justify-content:center;gap:36px;color:var(--white);font-size:14px}
.legal{left:0;top:3876px;width:1200px;text-align:center;color:var(--white);font-size:12px}
</style>
</head>
<body>

<!-- navigation -->
<header class="abs topbar"></header>
<div class="abs brand"><div class="name">CALDER</div><div class="sub">AVIATION</div></div>
<nav class="abs nav"><span>Home</span><span>What We Do</span><span>Who We Are</span><span>Latest News</span><span>Contact Us</span></nav>
<div class="abs btn-outline nav-cta">Get Started Now</div>

<!-- hero -->
<svg class="abs hero" viewBox="0 0 1200 680" aria-hidden="true">
  <path d="M0 0H1200V558Q600 760 0 558Z" fill="#6aaed8"/>
  <path d="M0 558Q600 760 1200 558V578Q600 790 0 578Z" fill="#0b1740"/>
</svg>
<div class="abs hero-art" role="img" aria-label="Illustration of a wide-body freighter in flight among white clouds"></div>
<div class="abs hero-kicker">We are involved in</div>
<h1 class="abs hero-title">COMMERCIAL AIRCRAFT.</h1>
<div class="abs btn-navy hero-btn">Learn More</div>
<div class="abs dots"><i></i><i class="on"></i><i></i><i></i></div>

<!-- what we do -->
<div class="abs ghost" style="top:840px" aria-hidden="true">SERVICS</div>
<h2 class="abs sec-title" style="top:866px">WHAT WE DO</h2>
<p class="abs sec-sub" style="top:929px">Calder has deep industry relationships and years of expertise, allowing to<br>successfully execute lease transactions.</p>

<article class="abs card" style="left:111px">
  <div class="ph" role="img" aria-label="Model aircraft resting on a calculator beside coins" style="background:linear-gradient(135deg,#3a7bc0 0%,#c9d2dc 45%,#e9ecef 100%)"></div>
  <h3>AIRCRAFT FINANCE</h3>
  <p>Lorem Ipsum is simply dummy text of the printing and typesetting industry. Lorem Ipsum has been the industry's standard dummy text ever since the 1500s, when an unknown printer</p>
  <div class="btn">Learn More</div>
</article>
<article class="abs card lift" style="left:443px">
  <div class="ph" role="img" aria-label="Airliners parked at an airport terminal" style="background:linear-gradient(180deg,#b8c4d2 0%,#6f7b88 45%,#84858a 70%,#9a9590 100%)"></div>
  <h3>TRADING</h3>
  <p>Lorem Ipsum is simply dummy text of the printing and typesetting industry. Lorem Ipsum has been the industry's standard dummy text ever since the 1500s, when an unknown printer</p>
  <div class="btn">Learn More</div>
</article>
<article class="abs card" style="left:774px">
  <div class="ph" role="img" aria-label="Airliner climbing through a blue sky" style="background:linear-gradient(180deg,#5d95d0 0%,#a7c6e6 60%,#cfe0f1 100%)"></div>
  <h3>PROCUREMENT &amp; LEASING</h3>
  <p>Lorem Ipsum is simply dummy text of the printing and typesetting industry. Lorem Ipsum has been the industry's standard dummy text ever since the 1500s, when an unknown printer</p>
  <div class="btn">Learn More</div>
</article>

<!-- who we are -->
<section class="abs about" role="img" aria-label="Faint aircraft fuselage behind the section"></section>
<div class="abs ghost about-ghost" style="top:1712px" aria-hidden="true">ABOUT US</div>
<h2 class="abs sec-title" style="top:1740px;color:var(--white)">WHO WE ARE</h2>
<p class="abs sec-sub" style="top:1802px;color:var(--white)">Founded in 2011, Calder Aviation’s management has many years of experi-<br>ence in Aviation, a strong background in scheduled airlines</p>
<div class="abs about-copy">
  <p>Calder’s focuses in facilitating wet and dry lease oper-ations, charter and ACMI programs consultancy, aircraft sales, leasing and procurement, aviation consultancy and aircraft management.</p>
  <p>Calder team is a hands-on reliable alternative that works toward achieving your aircraft and aviation objec-tives by meeting your requirements and timeframe throughout professional and personalized service.</p>
</div>
<div class="abs btn-outline about-btn">Get Started Now</div>
<div class="abs about-media" role="img" aria-label="Video still: handshake in front of a parked business jet"></div>
<svg class="abs" style="left:827px;top:2028px" width="52" height="52" viewBox="0 0 52 52" aria-label="Play video"><circle cx="26" cy="26" r="25" fill="#fff"/><path d="M20 15L37 26L20 37Z" fill="#000"/></svg>

<!-- blog -->
<div class="abs ghost" style="top:2384px" aria-hidden="true">LATEST</div>
<h2 class="abs sec-title" style="top:2412px">BLOG &amp; NEWS</h2>
<p class="abs sec-sub" style="top:2477px">Lorem Ipsum is simply dummy text of the printing and typesetting industry.<br>Lorem Ipsum has been the industry's standard dummy text</p>

<article class="abs feature" role="img" aria-label="City skyline at dusk">
  <h4>Neque porro quisquam est qui dolorem ipsum quia dolor sit amet, adipisci velit...</h4>
  <a>Read More &gt;</a>
</article>
<div class="abs mini-ph" style="top:2561px;background:linear-gradient(135deg,#e9e5df 0%,#b7aea4 50%,#6e6a66 100%)" role="img" aria-label="Two colleagues reviewing documents"></div>
<div class="abs mini-text" style="top:2565px"><h4>Neque porro quisquam est qui dolorem ipsum ipisci velit...</h4><a>Read More &gt;</a></div>
<div class="abs mini-ph" style="top:2758px;background:linear-gradient(135deg,#1f1a12 0%,#8a5a2e 50%,#d39b66 100%)" role="img" aria-label="Stacks of coins"></div>
<div class="abs mini-text" style="top:2762px"><h4>Neque porro quisquam est qui dolorem ipsum ipisci velit...</h4><a>Read More &gt;</a></div>

<!-- contact -->
<section class="abs contact" role="img" aria-label="Aircraft flying over a coastline at dusk"></section>
<h2 class="abs contact-title">CONTACT &nbsp;US</h2>
<p class="abs contact-info" style="top:3249px;font-size:13.5px">Lorem Ipsum is simply dummy text of the printing and<br>typesetting industry. Lorem Ipsum has been the<br>industry's standard dummy text ever since the 1500s,</p>
<p class="abs contact-info" style="top:3354px;font-size:17px">Address</p>
<p class="abs contact-info" style="top:3384px;font-size:15px;line-height:23px">
  <svg width="18" height="12" viewBox="0 0 18 12" aria-hidden="true"><path d="M1 2L6 1L12 3L17 1V10L12 11L6 9L1 11Z" fill="none" stroke="#fff" stroke-width="1.3"/><path d="M6 1V9M12 3V11" stroke="#fff" stroke-width="1.3"/></svg>
  - 48 Larkin Row Suite 210,<br>Westbrook Harbor, 30418.</p>
<p class="abs contact-info" style="top:3457px;font-size:15px">
  <svg width="14" height="14" viewBox="0 0 14 14" aria-hidden="true"><path d="M3 1L6 4L4.5 6Q6 9 8 9.5L10 8L13 11L11 13Q5 13 1 3Z" fill="#fff"/></svg>
  - 1-555-014-2290</p>
<p class="abs contact-info" style="top:3505px;font-size:13px">
  <svg width="15" height="11" viewBox="0 0 15 11" aria-hidden="true"><rect x="1" y="1" width="13" height="9" fill="none" stroke="#fff" stroke-width="1.3"/><path d="M1 1L7.5 6L14 1" fill="none" stroke="#fff" stroke-width="1.3"/></svg>
  - hello@calderaviation.com</p>
<div class="abs socials" aria-label="Social links"><span></span><span></span><span></span><span></span><span></span></div>
<div class="abs btn-outline contact-cta">Get Started!</div>

<form class="abs form">
  <h5>Contact Us Today!</h5>
  <div class="field" style="top:82px;height:49px">Email</div>
  <div class="field" style="top:143px;height:49px">Phone</div>
  <div class="field" style="top:204px;height:109px">Message</div>
  <div class="btn-navy send">Get Started!</div>
</form>

<!-- footer -->
<footer class="abs footer"></footer>
<nav class="abs foot-nav"><span>Home</span><span>What We Do</span><span>Who We Are</span><span>Latest News</span><span>Contact Us</span></nav>
<p class="abs legal">Terms of Service | Privacy Policy | Return Policy | Accessibility. Copyright © 2021 Calder Aviation.</p>

</body>
</html>
```